Business Card Design for Occupational Medicine Start Up Company

We need to design a professional business card. We are a healthcare company providing occupational medicine services to blue collar industries. We are professional, efficient and high quality service providers.

Target Market(s)

Blue Collar Industry: Shipbuilding, Ports, Trucking Companies; The Executives and Safety Officers for these companies

Industry/Entity Type

Healthcare

Contact Information for Business Card

Logo, Name, Title, Email, Phone

Other font styles liked:
• Please match our Brand Guide

Requirements
Must have
• Our Company Colors and Logo

```html
<!DOCTYPE html>
<html lang="en">
<head>
<meta charset="utf-8">
<title>Crewline Health – Business Card</title>
<link rel="stylesheet" href="https://fonts.googleapis.com/css2?family=Montserrat:wght@400;500;700;800&display=swap">
<style>
  :root {
    --navy: #2e2c7a;
    --ink: #2b2a6b;
    --sky: #1f9fe0;
    --amber: #f5b335;
    --paper: #ffffff;
    --stage: #e9e9ec;
    --body: #3a3a4a;
    --faint: #eceaf4;
  }
  * { margin: 0; padding: 0; box-sizing: border-box; }
  html, body { width: 1200px; height: 1186px; overflow: hidden; }
  body {
    background: var(--stage);
    font-family: "Montserrat", sans-serif;
    position: relative;
  }
  .card {
    position: absolute;
    left: 150px;
    width: 900px;
    height: 514px;
    border-radius: 28px;
    overflow: hidden;
    box-shadow: 0 10px 30px rgba(0,0,0,.15);
  }
  .card--back { top: 60px; background: var(--navy); }
  .card--front { top: 612px; background: var(--paper); }

  .brand {
    position: absolute;
    display: flex;
    align-items: center;
    gap: 18px;
    font-weight: 800;
    letter-spacing: 1px;
    text-transform: uppercase;
    white-space: nowrap;
  }
  .brand__dot { border-radius: 50%; flex: none; }
  .card--back .brand {
    left: 50%; top: 50%;
    transform: translate(-50%, -50%);
    color: var(--paper);
    font-size: 64px;
  }
  .card--back .brand__dot { width: 58px; height: 58px; background: var(--amber); }
  .card--front .brand {
    left: 60px; top: 70px;
    color: var(--navy);
    font-size: 44px;
  }
  .card--front .brand__dot { width: 40px; height: 40px; background: var(--sky); }

  .decor-circle {
    position: absolute;
    right: -90px; top: -120px;
    width: 380px; height: 380px;
    border-radius: 50%;
    background: var(--faint);
    opacity: .7;
  }

  .divider {
    position: absolute;
    left: 40px; right: 40px; top: 300px;
    height: 3px;
    display: flex;
  }
  .divider span { flex: 1; }
  .divider .seg-sky { background: var(--sky); }
  .divider .seg-navy { background: var(--navy); }
  .divider .seg-amber { background: var(--amber); }

  .person { position: absolute; left: 60px; top: 220px; }
  .person__name { font-size: 32px; font-weight: 800; color: var(--ink); line-height: 1.1; }
  .person__title { font-size: 19px; font-weight: 400; color: var(--body); margin-top: 2px; }

  .address {
    position: absolute;
    right: 60px; top: 236px;
    text-align: right;
    font-size: 18px;
    line-height: 1.35;
    color: var(--body);
  }

  .contacts {
    position: absolute;
    left: 60px; top: 330px;
    list-style: none;
    font-size: 20px;
    color: var(--body);
  }
  .contacts li { display: flex; align-items: center; gap: 14px; height: 36px; }
  .contacts svg { width: 18px; height: 18px; fill: var(--sky); flex: none; }
</style>
</head>
<body>

  <section class="card card--back" aria-label="Card back">
    <div class="brand"><span class="brand__dot"></span>Crewline Health</div>
  </section>

  <section class="card card--front" aria-label="Card front">
    <div class="decor-circle"></div>

    <div class="brand"><span class="brand__dot"></span>Crewline Health</div>

    <div class="person">
      <p class="person__name">Daniel Reyes</p>
      <p class="person__title">CEO &amp; Founder</p>
    </div>

    <p class="address">418 Harbor View Rd, #12<br>Lakeport, OH 43000</p>

    <div class="divider">
      <span class="seg-sky"></span><span class="seg-navy"></span><span class="seg-amber"></span>
    </div>

    <ul class="contacts">
      <li>
        <svg viewBox="0 0 24 24" aria-hidden="true"><path d="M6.6 10.8a15.1 15.1 0 0 0 6.6 6.6l2.2-2.2c.3-.3.7-.4 1-.2 1.1.4 2.3.6 3.6.6.6 0 1 .4 1 1V20c0 .6-.4 1-1 1A17 17 0 0 1 3 4c0-.6.4-1 1-1h3.5c.6 0 1 .4 1 1 0 1.3.2 2.5.6 3.6.1.3 0 .7-.2 1z"/></svg>
        800-555-0142
      </li>
      <li>
        <svg viewBox="0 0 24 24" aria-hidden="true"><path d="M2 5h20v14H2zm2 2v.5l8 5 8-5V7l-8 5z"/></svg>
        hello@crewlinehealth.com
      </li>
      <li>
        <svg viewBox="0 0 24 24" aria-hidden="true"><circle cx="12" cy="12" r="10"/></svg>
        www.crewlinehealth.com
      </li>
    </ul>
  </section>

</body>
</html>
```